Flyer for Medical practice welcoming new patients

We need a DL size brochure designed for Medical practice to advertise that we are accepting new patients. Our practice has special interests in women's and children's health and seniors health. Our existing advertising materials are in the colour scheme of purples I have uploaded our logo which includes our colour scheme.

Target Market(s)

Versatile to target anyone looking for a small medical practice that offers continuous care of seeing the same Doctor every time

Industry/Entity Type

Advertising

Font styles to use
Serif

Colors
6b449b
876aae
b7a5cc

Requirements
Must have
• The practice logo of just the picture not Dr Petra Holcombe.
• Purple colour scheme.
• Practice name: Tarrabeen Medical Practice.
• Address: 147 Corlett Rd, Tarrabeen NSW 2500.
• Phone: 4871 6035.
• DL size brochure
• Welcoming new patients ( a strong emphasis needs to be placed on this)
• Nurse and onsite ECG's and lung function tests.
• Travel vaccines including yellow fever
• Bulk billing for tertiary students
• We would also like design to alter the text so that we can change the points to be reflect who we are targeting at the time.
Nice to have
• The practice logo with Dr Petra Holcombe somewhere not as a feature as the practice no longer goes under this name but is still well known as Dr Holcombe's.

```html
<!DOCTYPE html>
<html lang="en">
<head>
<meta charset="utf-8">
<title>Tarrabeen Medical Practice – DL Flyer</title>
<link rel="stylesheet" href="https://fonts.googleapis.com/css2?family=Carlito:wght@400;700&family=Oswald:wght@600&family=Didact+Gothic&display=swap">
<style>
  :root {
    --purple-deep: #5a3690;
    --purple: #6b449b;
    --purple-mid: #876aae;
    --purple-soft: #b7a5cc;
    --lavender: #ddd3ea;
    --plum: #6a2b7f;
    --line-grey: #a9a6ad;
    --page: #e4e4e6;
    --white: #ffffff;
  }
  * { margin: 0; padding: 0; box-sizing: border-box; }
  html, body { width: 1200px; height: 1000px; overflow: hidden; }
  body { background: var(--page); position: relative; font-family: "Carlito", "Calibri", sans-serif; }

  .flyer {
    position: absolute; left: 381px; top: 40px;
    width: 438px; height: 920px;
    background: var(--white);
    overflow: hidden;
  }
  .flyer__waves { position: absolute; inset: 0; }

  .brand { position: absolute; right: 11px; top: 30px; text-align: right; }
  .brand__mark {
    display: block; width: 160px; height: 160px; margin: 0 41px 10px auto;
    border: 3px solid var(--lavender); border-radius: 50%;
  }
  .brand__name {
    font-family: "Carlito", "Calibri", sans-serif; font-weight: 400;
    color: var(--plum); font-size: 27px; line-height: 30px;
  }

  .badge { position: absolute; left: 4px; top: 267px; width: 210px; height: 210px; }
  .badge__text {
    position: absolute; inset: 0; display: flex; flex-direction: column;
    align-items: center; justify-content: center;
    color: var(--white); font-size: 27px; line-height: 40px; letter-spacing: 0.5px;
    text-shadow: 0 1px 2px rgba(40,20,70,.6);
  }

  .service { position: absolute; color: var(--purple-deep); font-weight: 700; font-size: 19px; line-height: 22px; }
  .service::before {
    content: ""; position: absolute; left: -16px; top: 6px;
    width: 9px; height: 9px; border-radius: 50%; background: var(--purple);
  }
  .service--nurse { left: 38px; top: 486px; width: 390px; }
  .service--travel { left: 135px; top: 548px; width: 300px; }
  .service--travel .indent { padding-left: 27px; }
  .service--billing { left: 232px; top: 620px; width: 200px; line-height: 19px; }

  .contact { position: absolute; left: 11px; top: 692px; color: var(--purple-deep); }
  .contact__title { font-family: "Oswald", "Arial Narrow", sans-serif; font-weight: 600; font-size: 16px; letter-spacing: -.2px; }
  .contact__label {
    font-family: "Didact Gothic", "Century Gothic", sans-serif;
    color: var(--purple-mid); font-size: 18px; letter-spacing: 1px; margin-top: 20px;
  }
  .contact__label + .contact__value { margin-top: 6px; }
  .contact__label--phone { margin-top: 12px; }
  .contact__value { font-family: "Didact Gothic", "Century Gothic", sans-serif; font-size: 14px; line-height: 22px; letter-spacing: .4px; }
</style>
</head>
<body>
  <main class="flyer">
    <svg class="flyer__waves" width="438" height="920" viewBox="0 0 438 920" aria-hidden="true">
      <defs>
        <linearGradient id="mid-zone" x1="0" y1="0" x2="0" y2="1">
          <stop offset="0" stop-color="#ffffff"/>
          <stop offset="1" stop-color="#d6cbe5"/>
        </linearGradient>
        <linearGradient id="wave-fill" x1="0" y1="0" x2="1" y2="1">
          <stop offset="0" stop-color="#a48dc6"/>
          <stop offset=".55" stop-color="#7c5bb0"/>
          <stop offset="1" stop-color="#5e3a96"/>
        </linearGradient>
        <linearGradient id="wave-fill-low" x1="0" y1="0" x2="0" y2="1">
          <stop offset="0" stop-color="#6b449b"/>
          <stop offset="1" stop-color="#a590c8"/>
        </linearGradient>
        <linearGradient id="badge-fill" x1="0" y1="0" x2="0" y2="1">
          <stop offset="0" stop-color="#a58cc9"/>
          <stop offset="1" stop-color="#5f3a94"/>
        </linearGradient>
      </defs>

      <path class="mid-zone" fill="url(#mid-zone)"
        d="M0,235 C20,215 40,205 70,203 C170,196 300,330 438,372 L438,690 C400,760 360,780 300,720 C220,640 120,560 0,570 Z"/>

      <path class="wave-top" fill="url(#wave-fill)"
        d="M0,84 C100,84 150,278 270,286 C340,290 400,288 438,296 L438,372 C300,330 170,196 70,203 C40,205 20,215 0,235 Z"/>
      <path fill="none" stroke="var(--line-grey)" stroke-width="5"
        d="M0,238 C20,218 40,208 70,206 C170,199 300,333 438,376"/>
      <path fill="none" stroke="#4c2d7c" stroke-width="4"
        d="M0,84 C100,84 150,278 270,286 C340,290 400,288 438,296"/>

      <path class="wave-bottom" fill="url(#wave-fill-low)"
        d="M0,570 C120,560 220,640 300,720 C360,780 400,760 438,690 L438,872 C400,880 330,872 280,842 C180,782 100,618 0,604 Z"/>
      <path fill="none" stroke="var(--line-grey)" stroke-width="5"
        d="M0,566 C120,556 220,636 300,716 C360,776 400,756 438,686"/>
      <path fill="none" stroke="#4c2d7c" stroke-width="4"
        d="M0,604 C100,618 180,782 280,842 C330,872 400,880 438,872"/>

      <polygon class="corner" fill="var(--purple-soft)" points="364,0 438,0 438,42"/>
      <line x1="366" y1="2" x2="438" y2="44" stroke="#6a5a80" stroke-width="4"/>
      <polygon class="corner" fill="var(--purple-soft)" points="0,879 0,920 64,920"/>
      <line x1="0" y1="876" x2="66" y2="920" stroke="#6a5a80" stroke-width="4"/>
    </svg>

    <header class="brand">
      <span class="brand__mark"></span>
      <div class="brand__name">Tarrabeen<br>Medical Practice</div>
    </header>

    <div class="badge">
      <svg width="210" height="210" viewBox="-105 -105 210 210" aria-hidden="true">
        <polygon fill="var(--white)" stroke="#9a95a0" stroke-width="1.5"
          points="0,-104 9,-86 26,-101 30,-81 49,-92 48,-72 69,-78 62,-59 84,-60 73,-43 95,-39 79,-26 99,-17 81,-8 100,5 80,12 96,25 76,30 88,46 67,47 75,65 55,62 58,82 39,74 38,96 22,83 16,103 5,86 -5,103 -12,84 -23,99 -27,80 -42,93 -42,72 -60,81 -56,62 -75,66 -66,48 -88,45 -75,31 -96,24 -80,12 -100,4 -81,-8 -99,-17 -79,-26 -95,-39 -73,-43 -84,-60 -62,-59 -69,-78 -48,-72 -49,-92 -30,-81 -26,-101 -9,-86"/>
        <polygon fill="url(#badge-fill)" transform="scale(.9)"
          points="0,-104 9,-86 26,-101 30,-81 49,-92 48,-72 69,-78 62,-59 84,-60 73,-43 95,-39 79,-26 99,-17 81,-8 100,5 80,12 96,25 76,30 88,46 67,47 75,65 55,62 58,82 39,74 38,96 22,83 16,103 5,86 -5,103 -12,84 -23,99 -27,80 -42,93 -42,72 -60,81 -56,62 -75,66 -66,48 -88,45 -75,31 -96,24 -80,12 -100,4 -81,-8 -99,-17 -79,-26 -95,-39 -73,-43 -84,-60 -62,-59 -69,-78 -48,-72 -49,-92 -30,-81 -26,-101 -9,-86"/>
      </svg>
      <div class="badge__text"><span>ACCEPTING</span><span>NEW</span><span>PATIENT!</span></div>
    </div>

    <p class="service service--nurse">Nurse on site for ECG's, lung function tests,<br>health assessments and much more</p>
    <p class="service service--travel">We offer travel vaccines including<br><span class="indent">yellow fever</span></p>
    <p class="service service--billing">Bulk billing for tertiary<br>students</p>

    <section class="contact">
      <h2 class="contact__title">Contact Details:</h2>
      <p class="contact__label">Address:</p>
      <p class="contact__value">147 Corlett Rd,<br>Tarrabeen NSW 2500.</p>
      <p class="contact__label contact__label--phone">Telephone:</p>
      <p class="contact__value">4871 6035</p>
    </section>
  </main>
</body>
</html>
```